Awesome business card design needed

We need a new business card design to go with our new logo.
We are a web development agency that specialises in highly complex back-end integrations as opposed to design, our customers are retailers, hotels, hospitals and any other organisation that has a large online marketing department.
Take a look at our website - www.brenoloft.com for some inspiration.
We want our new business cards to exude class, professionalism and style.
We are likely to choose a high-end card to print them on but we want the design of the card itself to really turn heads.
We have no specific colour requirements, the logo as you will see is a turquoise colour R89 G171 B167 #59aba7 but it can also be in white if you want to make the colour of the card something different.
The information on the card should be:
Name
Position
Tel
email
Potentially a double sided card could have our web address, twitter and FB links.

```html
<!DOCTYPE html>
<html lang="en">
<head>
<meta charset="utf-8">
<title>Brenoloft business cards</title>
<link rel="stylesheet" href="https://fonts.googleapis.com/css2?family=Mulish:wght@400;800&display=swap">
<style>
  :root {
    --teal: #59aba7;
    --charcoal: #4a4a4c;
    --ink: #3a3a3c;
    --paper: #ffffff;
    --backdrop: #e9e8ee;
    --rule: #c9c9cc;
  }
  * { margin: 0; padding: 0; box-sizing: border-box; }
  html, body {
    width: 1200px; height: 987px; overflow: hidden;
    background: var(--backdrop);
    font-family: "Mulish", sans-serif;
  }
  .card {
    position: absolute;
    width: 640px; height: 366px;
    background: var(--paper);
    border-radius: 22px;
    overflow: hidden;
    box-shadow: 0 6px 18px rgba(0,0,0,.12);
  }
  .card--front { left: 280px; top: 520px; }
  .card--back  { left: 280px; top: 100px; }

  .wordmark {
    position: absolute;
    color: var(--teal);
    font-weight: 800;
    letter-spacing: 2px;
    line-height: 1;
  }
  .card--front .wordmark { left: 70px; top: 20px; font-size: 88px; }
  .card--back .wordmark  { left: 0; right: 0; top: 70px; font-size: 104px; text-align: center; }

  .wave { position: absolute; left: 0; top: 0; width: 640px; height: 366px; }

  .address {
    position: absolute; right: 400px; top: 128px;
    text-align: right; color: var(--ink);
    font-style: normal; font-size: 16px; line-height: 22px;
  }
  .divider {
    position: absolute; left: 254px; top: 128px;
    width: 1px; height: 70px; background: var(--rule);
  }
  .contacts {
    position: absolute; left: 268px; top: 126px;
    list-style: none; color: var(--ink);
    font-size: 18px; line-height: 24px;
  }
  .contacts li { display: flex; align-items: center; gap: 8px; }
  .contacts svg { width: 14px; height: 14px; flex: none; }

  .person {
    position: absolute; right: 40px; bottom: 16px;
    color: var(--paper); text-align: right;
  }
  .person__name { font-size: 24px; font-weight: 800; line-height: 1.1; }
  .person__role { font-size: 17px; line-height: 1.2; }

  .follow {
    position: absolute; left: 0; right: 0; top: 212px;
    text-align: center; color: var(--teal);
    font-size: 19px; font-weight: 800; letter-spacing: 2px;
  }
  .web-row {
    position: absolute; left: 0; right: 0; top: 250px;
    display: flex; justify-content: center; align-items: center; gap: 14px;
    color: var(--ink); font-size: 19px; letter-spacing: 3px;
  }
  .web-row strong { color: var(--teal); font-weight: 800; }
  .social { display: flex; gap: 10px; }
  .social span {
    width: 34px; height: 34px; border-radius: 8px;
    background: var(--teal);
  }
</style>
</head>
<body>

<section class="card card--back" aria-label="Card back">
  <div class="wordmark">brenoloft</div>
  <p class="follow">Follow Us On:</p>
  <div class="web-row">
    <span>www.<strong>brenoloft</strong>.com</span>
    <span class="social" aria-label="Social network links"><span></span><span></span></span>
  </div>
</section>

<section class="card card--front" aria-label="Card front">
  <svg class="wave" viewBox="0 0 640 366" aria-hidden="true">
    <path d="M0,200 C200,204 440,228 640,272" stroke="var(--teal)" stroke-width="5" fill="none"/>
    <path fill="var(--charcoal)" d="M0,212 C150,214 300,228 440,262 C300,238 150,232 0,234 Z"/>
    <path fill="var(--teal)" d="M0,248 C200,252 420,262 640,292 L640,366 L0,366 Z"/>
  </svg>

  <div class="wordmark">brenoloft</div>

  <address class="address">
    Street Name<br>City Name<br>State Zip Code
  </address>
  <div class="divider"></div>

  <ul class="contacts">
    <li>
      <svg viewBox="0 0 14 14"><circle cx="7" cy="7" r="7" fill="var(--teal)"/><path d="M4.5 3.5c.5-.5 1-.4 1.3.1l.6 1.1c.2.4 0 .7-.3 1l-.3.3c.3.8 1 1.5 1.8 1.8l.3-.3c.3-.3.6-.5 1-.3l1.1.6c.5.3.6.8.1 1.3-1.6 1.6-6.8-3.4-5.6-5.6z" fill="#fff"/></svg>
      123-456-7890
    </li>
    <li>
      <svg viewBox="0 0 14 14"><circle cx="7" cy="7" r="7" fill="var(--teal)"/><rect x="3.5" y="4.5" width="7" height="5" fill="#fff"/><path d="M3.5 4.5 7 7.3 10.5 4.5" stroke="var(--teal)" stroke-width=".8" fill="none"/></svg>
      info@brenoloft.com
    </li>
    <li>
      <svg viewBox="0 0 14 14"><circle cx="7" cy="7" r="7" fill="var(--teal)"/><circle cx="7" cy="7" r="4" stroke="#fff" stroke-width=".9" fill="none"/><path d="M3 7h8M7 3c-2 2.5-2 5.5 0 8M7 3c2 2.5 2 5.5 0 8" stroke="#fff" stroke-width=".8" fill="none"/></svg>
      www.brenoloft.com
    </li>
  </ul>

  <div class="person">
    <div class="person__name">Your Name</div>
    <div class="person__role">Position</div>
  </div>
</section>

</body>
</html>
```